Dermatology at Your Door Logo and business card

We provide dermatological services to the community. This includes Assisted Living Facilities, nursing homes and to large cooperation, Health fairs etc. We provide a health care provider that travels to institutions, providing these services. All procedures and surgeries are done onsite in one of our state of the art mobile clinics. We provide services including, but not limited to; skin biopsies, skin surgeries , surgical procedures including skin cancer removal mole removal and treatment of various skin disorders. we bring mobile Dermatology to you.

Industry/Entity Type

Business

Contact Information for Business Card

Need Logo address phone number, email website

Logo Text

Dermatology at Your Door

Logo styles of interest
Emblem Logo
Abstract Logo
Character Logo
Lettermark Logo
Requirements
Must have
• Marcus Tilden ARNP DN-C
• Medical Facilitator
• P. (407) 555-3914
• Fax (386) 555-7281

```html
<!DOCTYPE html>
<html lang="en">
<head>
<meta charset="utf-8">
<title>Dermatology at Your Door – Business Card</title>
<link rel="stylesheet" href="https://fonts.googleapis.com/css2?family=Arimo:wght@400&display=swap">
<style>
  :root {
    --paper: #ffffff;
    --card-teal: #0f5d5b;
    --card-teal-glow: #2a7a76;
    --brand-aqua: #4fc2ba;
    --text-white: #ffffff;
  }
  * { margin: 0; padding: 0; box-sizing: border-box; }
  html, body {
    width: 1200px;
    height: 703px;
    overflow: hidden;
    background: var(--paper);
  }
  .card {
    position: absolute;
    left: 19px;
    top: 20px;
    width: 1162px;
    height: 662px;
    background: var(--card-teal);
    overflow: hidden;
  }
  .card__texture {
    position: absolute;
    left: 0;
    right: 0;
    bottom: 0;
    height: 330px;
    background:
      radial-gradient(ellipse 60% 70% at 30% 70%, rgba(255,255,255,0.07), transparent 70%),
      radial-gradient(ellipse 50% 60% at 80% 75%, rgba(255,255,255,0.06), transparent 70%),
      linear-gradient(to bottom, rgba(42,122,118,0) 0%, var(--card-teal-glow) 100%);
    opacity: 0.8;
  }
  .brand {
    position: absolute;
    left: 0;
    right: 0;
    top: 190px;
    display: flex;
    align-items: center;
    justify-content: center;
    gap: 28px;
  }
  .brand__mark {
    width: 84px;
    height: 84px;
    border-radius: 50%;
    background: var(--brand-aqua);
    flex: none;
  }
  .brand__name {
    font-family: "Arimo", Arial, sans-serif;
    font-weight: 400;
    font-size: 58px;
    line-height: 1;
    color: var(--text-white);
    white-space: nowrap;
  }
  .person {
    position: absolute;
    left: 60px;
    top: 452px;
    width: 460px;
    text-align: center;
    font-family: "Arimo", Arial, sans-serif;
    color: var(--text-white);
  }
  .person__name {
    font-size: 46px;
    line-height: 1;
    letter-spacing: 0.5px;
    white-space: nowrap;
  }
  .person__credentials {
    margin-top: 14px;
    font-size: 24px;
    line-height: 1;
    letter-spacing: 0.5px;
  }
  .person__role {
    margin-top: 10px;
    font-size: 28px;
    line-height: 1;
    letter-spacing: 2px;
  }
  .contact {
    position: absolute;
    right: 60px;
    top: 462px;
    list-style: none;
    font-family: "Arimo", Arial, sans-serif;
    color: var(--text-white);
  }
  .contact__item {
    display: flex;
    align-items: center;
    justify-content: flex-end;
    height: 42px;
    font-size: 26px;
    letter-spacing: 1.5px;
    white-space: nowrap;
  }
  .contact__icon {
    width: 30px;
    height: 30px;
    margin-left: 22px;
    fill: var(--text-white);
  }
</style>
</head>
<body>
  <main class="card">
    <div class="card__texture" role="img" aria-label="Soft pattern of translucent bubbles across the lower half of the card"></div>

    <header class="brand">
      <span class="brand__mark" aria-hidden="true"></span>
      <span class="brand__name">Dermatology at Your Door</span>
    </header>

    <section class="person">
      <div class="person__name">MARCUS TILDEN</div>
      <div class="person__credentials">ARNP DN-C</div>
      <div class="person__role">MEDICAL FACILITATOR</div>
    </section>

    <ul class="contact">
      <li class="contact__item">
        <span>1820 Harbor Ln. ste #5</span>
        <svg class="contact__icon" viewBox="0 0 24 24" aria-hidden="true">
          <path d="M12 1.5c-4.4 0-8 3.4-8 7.8 0 5.6 8 13.2 8 13.2s8-7.6 8-13.2c0-4.4-3.6-7.8-8-7.8zm0 11a3.3 3.3 0 1 1 0-6.6 3.3 3.3 0 0 1 0 6.6z"/>
        </svg>
      </li>
      <li class="contact__item">
        <span>(407) 555-3914</span>
        <svg class="contact__icon" viewBox="0 0 24 24" aria-hidden="true">
          <path d="M6.6 2.5l3 3.4c.5.6.5 1.4 0 2l-1.5 1.6c1.3 2.6 3.3 4.6 5.9 5.9l1.6-1.5c.6-.5 1.4-.5 2 0l3.4 3c.6.5.6 1.4.1 2l-1.6 1.8c-.7.8-1.9 1.1-2.9.7C9.9 19.3 4.7 14.1 2.6 7.4c-.3-1 0-2.2.7-2.9L5 2.9c.5-.5 1.2-.5 1.6-.4z"/>
        </svg>
      </li>
      <li class="contact__item">
        <span>(386) 555-7281</span>
        <svg class="contact__icon" viewBox="0 0 24 24" aria-hidden="true">
          <path d="M6 2h9l3 3v4H6zM3 10h18a1 1 0 0 1 1 1v7H2v-7a1 1 0 0 1 1-1zm3 3v1.5h2V13zm4 0v1.5h2V13zm4 0v1.5h4V13zM2 19h20v3H2z"/>
        </svg>
      </li>
    </ul>
  </main>
</body>
</html>
```